PWNF Traditional Business Card Project

Please see attached....just a simple business card... on attachment- please use the exact font, style, etc as the attached "Ned Farley Broughton" card... however, replace with the "Walter Augustin Pryde" text and address below the card.

```html
<!DOCTYPE html>
<html lang="en">
<head>
<meta charset="utf-8">
<title>PWNF Business Card – Walter Augustin Pryde</title>
<link rel="stylesheet" href="https://fonts.googleapis.com/css2?family=Old+Standard+TT:wght@400;700&family=Questrial&display=swap">
<style>
  :root {
    --page-bg: #6a6a6a;
    --card-bg: #ffffff;
    --ink: #1e1e1e;
    --ink-soft: #3c3c3c;
    --icon-fill: #222222;
  }
  * { margin: 0; padding: 0; box-sizing: border-box; }
  html, body {
    width: 1200px;
    height: 1200px;
    overflow: hidden;
  }
  body {
    background: var(--page-bg);
    position: relative;
  }
  .business-card {
    position: absolute;
    left: 190px;
    top: 367px;
    width: 821px;
    height: 467px;
    background: var(--card-bg);
    border-radius: 24px;
    color: var(--ink);
  }
  .firm-name {
    position: absolute;
    left: 37px;
    top: 40px;
    font-family: "Old Standard TT", serif;
  }
  .firm-name__primary {
    display: block;
    font-size: 36px;
    font-variant: small-caps;
    font-weight: 400;
    letter-spacing: 0.5px;
    line-height: 1;
  }
  .firm-name__secondary {
    display: block;
    margin-left: 85px;
    margin-top: 6px;
    font-size: 15px;
    font-weight: 700;
    letter-spacing: 0.6px;
    color: var(--ink-soft);
  }
  .attorney {
    position: absolute;
    left: 0;
    right: 0;
    top: 190px;
    text-align: center;
  }
  .attorney__name {
    font-family: "Old Standard TT", serif;
    font-weight: 700;
    font-size: 27px;
    letter-spacing: 0.8px;
    line-height: 1;
  }
  .attorney__title {
    margin-top: 18px;
    font-family: "Questrial", sans-serif;
    font-size: 19px;
    letter-spacing: 1.2px;
    color: var(--ink-soft);
  }
  .contact {
    position: absolute;
    font-family: "Questrial", sans-serif;
    font-size: 17px;
    letter-spacing: 1.4px;
    color: var(--ink-soft);
    list-style: none;
  }
  .contact li {
    display: flex;
    align-items: center;
    gap: 8px;
    height: 29px;
  }
  .contact--address { left: 37px; top: 336px; }
  .contact--direct { left: 524px; top: 336px; }
  .contact__small-caps {
    font-variant: small-caps;
    font-size: 19px;
  }
  .contact__icon {
    width: 19px;
    height: 19px;
    flex: none;
  }
</style>
</head>
<body>
  <article class="business-card">
    <header class="firm-name">
      <span class="firm-name__primary">Pacific Westridge</span>
      <span class="firm-name__secondary">NORTHFIELD FIRM, PLC</span>
    </header>

    <section class="attorney">
      <h1 class="attorney__name">WALTER AUGUSTIN PRYDE</h1>
      <p class="attorney__title">ATTORNEY AT LAW</p>
    </section>

    <ul class="contact contact--address">
      <li>2740 ALDER COURT, SUITE B</li>
      <li>MEADOW GLEN, CA 90217</li>
      <li class="contact__small-caps">
        <svg class="contact__icon" viewBox="0 0 20 20" aria-hidden="true">
          <circle cx="10" cy="10" r="10" fill="var(--icon-fill)"/>
          <circle cx="10" cy="10" r="5.5" fill="none" stroke="#fff" stroke-width="1.4"/>
          <path d="M4.5 10h11M10 4.5c-2.5 3-2.5 8 0 11M10 4.5c2.5 3 2.5 8 0 11" fill="none" stroke="#fff" stroke-width="1.1"/>
        </svg>
        www.pwnflaw.com
      </li>
    </ul>

    <ul class="contact contact--direct">
      <li>
        <svg class="contact__icon" viewBox="0 0 20 20" aria-hidden="true">
          <circle cx="10" cy="10" r="10" fill="var(--icon-fill)"/>
          <path d="M6.5 5.5l2 -.5 1.2 2.6-1.3 1c.6 1.4 1.6 2.4 3 3l1-1.3 2.6 1.2-.5 2c-4.5.3-8.3-3.5-8-8z" fill="#fff"/>
        </svg>
        (555) 201-4400
      </li>
      <li>
        <svg class="contact__icon" viewBox="0 0 20 20" aria-hidden="true">
          <circle cx="10" cy="10" r="10" fill="var(--icon-fill)"/>
          <rect x="7" y="4.5" width="6" height="3" fill="#fff"/>
          <rect x="5" y="8" width="10" height="5" rx="1" fill="#fff"/>
          <rect x="7" y="11.5" width="6" height="4" fill="#fff" stroke="var(--icon-fill)" stroke-width="0.8"/>
        </svg>
        (555) 201-5004
      </li>
      <li class="contact__small-caps">
        <svg class="contact__icon" viewBox="0 0 20 20" aria-hidden="true">
          <circle cx="10" cy="10" r="10" fill="var(--icon-fill)"/>
          <rect x="5" y="6.5" width="10" height="7" fill="#fff"/>
          <path d="M5 6.5l5 4 5-4" fill="none" stroke="var(--icon-fill)" stroke-width="1"/>
        </svg>
        wpryde@pwnflaw.com
      </li>
    </ul>
  </article>
</body>
</html>
```